KTWG application splash screen

We need a 1024x768 image for use as an application splash screen.
The image will be displayed full screen on an 10 inch industrial PC 1024x768 screen while our application is launching. The image should convey that the application is "Waiting for connection to Wi-Fi access point..." and include a graphic of the industrial PC connected to the access point via an Ethernet cable. A list of troubleshooting steps should be included at the bottom of the image. The troubleshooting steps should not be the main focus of the image and should be shown in a smaller font (but still readable at 1024x768 displayed on a 10 inch screen).
I will include a mock up of the general idea of what we are looking for as well as image files for the industrial PC, a screenshot of our application to show on the PC's screen and the AP.
For general look and feel and a sense of corporate branding please review our website https://marrowgatesoilworks.example/. The splash screen should reflect corporate branding.
Target Market(s)
Users of our application
Industry/Entity Type
Agriculture
Look and feel

```html
<!DOCTYPE html>
<html lang="en">
<head>
<meta charset="utf-8">
<title>KTWG – Waiting for Wi-Fi access point</title>
<link rel="stylesheet" href="https://fonts.googleapis.com/css2?family=Open+Sans:wght@400;600;700&display=swap">
<style>
  :root {
    --brand-green: #2bb673;
    --white: #ffffff;
    --cable: #0b0b0b;
    --device-dark: #2a2c2e;
    --device-mid: #4a4d50;
    --ap-light: #f4f5f4;
    --ap-shade: #d9dcda;
  }
  html, body {
    margin: 0;
    padding: 0;
    width: 1200px;
    height: 900px;
    overflow: hidden;
    background: var(--white);
  }
  .splash {
    position: relative;
    width: 1024px;
    height: 768px;
    transform: scale(1.171875);
    transform-origin: 0 0;
    font-family: "Open Sans", Arial, sans-serif;
    background: var(--white);
    overflow: hidden;
  }
  .backdrop {
    position: absolute;
    inset: 0;
  }
  .headline {
    position: absolute;
    left: 40px;
    top: 50px;
    width: 600px;
    margin: 0;
    text-align: center;
    color: var(--white);
    font-weight: 400;
    font-size: 58px;
    line-height: 62px;
  }
  .brand-name {
    position: absolute;
    left: 797px;
    top: 48px;
    width: 148px;
    height: 148px;
    display: flex;
    align-items: center;
    justify-content: center;
    color: var(--white);
    font-weight: 700;
    font-size: 40px;
    letter-spacing: 1px;
  }
  .cab-computer {
    position: absolute;
    left: 88px;
    top: 330px;
    width: 270px;
    height: 216px;
    border-radius: 14px;
    background: linear-gradient(160deg, var(--device-mid), var(--device-dark));
  }
  .access-point {
    position: absolute;
    left: 855px;
    top: 230px;
    width: 46px;
    height: 250px;
    border-radius: 8px;
    background: linear-gradient(90deg, var(--ap-shade), var(--ap-light) 45%, var(--ap-shade));
  }
  .label {
    position: absolute;
    margin: 0;
    color: var(--brand-green);
    font-size: 23px;
    font-weight: 400;
    white-space: nowrap;
  }
  .label--computer { left: 93px; top: 560px; }
  .label--cable { left: 478px; top: 474px; }
  .ap-caption {
    position: absolute;
    left: 803px;
    width: 154px;
    margin: 0;
    text-align: center;
    color: var(--white);
  }
  .ap-caption--role { top: 568px; font-size: 21px; line-height: 25px; }
  .ap-caption--model { top: 659px; font-size: 15.5px; line-height: 19px; }
  .troubleshooting {
    position: absolute;
    left: 45px;
    top: 624px;
    width: 730px;
    color: var(--white);
    font-size: 11.9px;
    line-height: 16px;
  }
  .troubleshooting h2 {
    margin: 0 0 9px;
    font-size: 12.5px;
    font-weight: 700;
  }
  .troubleshooting ul {
    margin: 0;
    padding: 0;
    list-style: none;
  }
  .troubleshooting li {
    position: relative;
    padding-left: 19px;
    white-space: nowrap;
  }
  .troubleshooting li::before {
    content: "\27A4";
    position: absolute;
    left: 0;
    top: 0;
    font-size: 12px;
  }
  .troubleshooting .steps { margin-left: 2px; }
  .troubleshooting .steps li { padding-left: 14px; }
  .troubleshooting .steps li::before {
    content: "\2794";
    font-size: 10px;
  }
</style>
</head>
<body>
<main class="splash">
  <svg class="backdrop" width="1024" height="768" viewBox="0 0 1024 768" aria-hidden="true">
    <polygon points="0,0 1024,0 1024,125 712,125 590,296 0,296" fill="var(--brand-green)"/>
    <polygon points="0,615 246,615 268,636 1024,636 1024,768 0,768" fill="var(--brand-green)"/>
    <rect x="778" y="28" width="188" height="700" rx="40" fill="var(--white)"/>
    <rect x="803" y="150" width="154" height="570" fill="var(--brand-green)"/>
    <rect x="797" y="48" width="148" height="148" rx="30" fill="var(--brand-green)"/>
    <polyline points="357,515 880,515 880,478" fill="none" stroke="var(--cable)" stroke-width="4"/>
    <line x1="832" y1="551" x2="918" y2="551" stroke="var(--white)" stroke-width="1.5"/>
    <line x1="832" y1="645" x2="918" y2="645" stroke="var(--white)" stroke-width="1.5"/>
  </svg>

  <h1 class="headline">Waiting for connection to Wi-Fi access point...</h1>

  <div class="brand-name">KTWG</div>

  <div class="cab-computer" role="img" aria-label="Photo of the rugged tractor cab computer showing the KTWG seeding application"></div>
  <div class="access-point" role="img" aria-label="Photo of the outdoor Wi-Fi access point with two antennas"></div>

  <p class="label label--computer">Tractor Cab Computer</p>
  <p class="label label--cable">Ethernet Cable</p>

  <p class="ap-caption ap-caption--role">Wi-Fi Access<br>Point</p>
  <p class="ap-caption ap-caption--model">NetArc<br>WAP-220 Outdoor</p>

  <section class="troubleshooting">
    <h2>Troubleshooting steps:</h2>
    <ul>
      <li>This screen should only be visible for a short time on boot.</li>
      <li>If this screen stays visible for more than a minute:
        <ul class="steps">
          <li>Verify that the Wi-Fi Access Point (AP) powers up when this system does (indicated by a green light on the side of the AP).</li>
          <li>Check the Ethernet cable between this system and the AP for damage, and replace it if necessary.</li>
          <li>Power-cycle this system and wait for it to reboot fully.</li>
          <li>If the issue persists, contact KTWG support for further assistance.</li>
        </ul>
      </li>
    </ul>
  </section>
</main>
</body>
</html>
```